Local fast-growing company in the service sector

We are looking for a modern business card design, which should also appear on our letterheads

Target Market(s)

Private and industrial sectors

Contact Information for Business Card

Vorname Name
Kellberger Str. 18
74219 Lindenhausen
Tel.: 07146-839214-0
Name@agentur-kvtl.de

Colors
9d9d9d
919191
aaaaaa

Requirements
Must have
• The logo (file) in silver

```html
<!DOCTYPE html>
<html lang="de">
<head>
<meta charset="utf-8">
<title>KVTL Visitenkarte</title>
<link rel="stylesheet" href="https://fonts.googleapis.com/css2?family=Lato:wght@400;700&display=swap">
<style>
  :root {
    --page-bg: #ececec;
    --silver-light: #e2e2e2;
    --silver-mid: #aaaaaa;
    --silver-base: #9d9d9d;
    --silver-dark: #6f6f6f;
    --ink: #111111;
    --disc-dark: #2e2e2e;
    --disc-mid: #4a4a4a;
    --disc-edge: #5c5c5c;
    --brand-silver: #c9c9c9;
  }
  * { box-sizing: border-box; margin: 0; padding: 0; }
  html, body {
    width: 1200px;
    height: 900px;
    overflow: hidden;
    background: var(--page-bg);
  }
  .canvas {
    width: 1200px;
    height: 900px;
    display: flex;
    align-items: center;
    justify-content: center;
  }
  .business-card {
    position: relative;
    width: 900px;
    height: 556px;
    overflow: hidden;
    font-family: "Lato", sans-serif;
    color: var(--ink);
    background:
      linear-gradient(118deg,
        var(--silver-dark) 0%,
        var(--silver-base) 14%,
        var(--silver-light) 34%,
        var(--silver-mid) 52%,
        var(--silver-light) 70%,
        var(--silver-base) 86%,
        var(--silver-dark) 100%);
    box-shadow: 0 10px 30px rgba(0,0,0,0.18);
  }
  .holder-name {
    position: absolute;
    left: 52px;
    top: 76px;
    font-size: 28px;
    font-weight: 700;
    letter-spacing: 0.2px;
  }
  .address {
    position: absolute;
    left: 52px;
    top: 292px;
    font-size: 23px;
    font-style: normal;
    line-height: 33px;
  }
  .contact-list {
    position: absolute;
    left: 50px;
    top: 384px;
    list-style: none;
    font-size: 23px;
    line-height: 34px;
  }
  .contact-list li {
    display: flex;
    align-items: center;
    gap: 8px;
  }
  .contact-list svg {
    width: 22px;
    height: 22px;
    fill: var(--ink);
    flex: none;
  }
  .brand-disc {
    position: absolute;
    left: 378px;
    top: 30px;
    width: 496px;
    height: 496px;
    border-radius: 50%;
    background: radial-gradient(circle at 45% 50%, var(--disc-mid) 0%, var(--disc-dark) 75%, var(--disc-edge) 100%);
    box-shadow: 0 0 0 2px rgba(255,255,255,0.25), inset 0 0 30px rgba(0,0,0,0.4);
  }
  .brand-name {
    position: absolute;
    left: 378px;
    top: 30px;
    width: 496px;
    height: 496px;
    display: flex;
    align-items: center;
    justify-content: center;
    font-family: "Lato", sans-serif;
    font-weight: 700;
    font-size: 92px;
    letter-spacing: 2px;
    color: var(--brand-silver);
  }
</style>
</head>
<body>
  <main class="canvas">
    <article class="business-card">
      <h1 class="holder-name">VORNAME NAME</h1>

      <address class="address">
        Kellberger Str. 18<br>
        74219 Lindenhausen
      </address>

      <ul class="contact-list">
        <li>
          <svg viewBox="0 0 24 24" aria-hidden="true"><path d="M6.6 10.8c1.4 2.8 3.8 5.1 6.6 6.6l2.2-2.2c.3-.3.7-.4 1-.2 1.1.4 2.3.6 3.6.6.6 0 1 .4 1 1V20c0 .6-.4 1-1 1C10.6 21 3 13.4 3 4c0-.6.4-1 1-1h3.5c.6 0 1 .4 1 1 0 1.3.2 2.5.6 3.6.1.3 0 .7-.2 1z"/></svg>
          07146-839214-0
        </li>
        <li>
          <svg viewBox="0 0 24 24" aria-hidden="true"><path d="M2 5h20v2l-10 6L2 7z M2 9l10 6 10-6v10H2z"/></svg>
          Name@agentur-kvtl.de
        </li>
        <li>
          <svg viewBox="0 0 24 24" aria-hidden="true"><circle cx="12" cy="12" r="9"/><path d="M3.5 12h17M12 3c-3 3-3 15 0 18M12 3c3 3 3 15 0 18" stroke="#aaaaaa" stroke-width="1.4" fill="none"/></svg>
          www.agentur-kvtl.de
        </li>
      </ul>

      <div class="brand-disc" role="img" aria-label="Round window showing a softly blurred interior photo in dark grey tones"></div>
      <div class="brand-name">KVTL</div>
    </article>
  </main>
</body>
</html>
```